Quintel Packaging Business Card

Project Overview
We are seeking a modern, minimalist business card that effectively represents our company while making a bold and lasting impression. The design should reflect trust, professionalism, and innovation, reinforcing our expertise in custom plastic manufacturing for warehouse and distribution centers.

Provided Assets & Specifications
Logo: We will provide our official logo for integration into the design.
Design Files: Photoshop (PSD) files for our printing specifications will be supplied.

Card Size & Material:
Dimensions: 3.5" x 2"
Material: 1/8" Radius Plastic Business Cards with 1/8" Rounded Corners
Clear plastic background—the design should strategically incorporate transparency.
Orientation: The card should be designed in landscape format for a sleek and professional presentation.

Design Requirements:
Logo Prominence
The logo must be the focal point of the card.
Space should be used effectively to draw attention to the logo while maintaining a minimalist layout.

Clear Plastic Integration
The transparent background should create the illusion of blank space, enhancing the modern and high-quality feel.
Avoid any frosted effects—we do not want white areas to appear semi-transparent.

Minimalist & Impactful
Clean, structured, and easy to read at a glance.
Focus on sharp contrast to ensure legibility and visibility.
The design should instill confidence and reflect our role as a leading plastics manufacturer.

Color Palette & Contrast
Primary Colors: Blue, Black, White, and Grey
Use bold black or blue for text and key elements to ensure they stand out against the clear plastic.
Avoid light, pastel, or neon colors that may fade into the plastic background.
No frosted or semi-transparent white—we do not want a cloudy effect.

Typography & Information Hierarchy
Bold, modern typography—clear, professional, and highly legible.
The business card should highlight:
Company Logo (Primary Focus)
Full Name & Title
Phone Number
Email
Website

Brand Representation
The card should reflect our expertise in manufacturing high-quality custom plastics for large-scale packaging and distribution businesses.
Our clients rely on us to enhance their brand presence through custom plastic solutions, and our business cards should reinforce that sense of precision and trust.

Final Considerations
Utilize the clear plastic effectively to differentiate our brand from standard business cards.
Maintain a sleek, professional aesthetic while ensuring all text and elements remain legible.
The design should align with our industry, conveying reliability and innovation.
We look forward to seeing a design that captures our brand identity, maximizes the clear plastic medium, and makes a strong, professional impact on our clients.

```html
<!DOCTYPE html>
<html lang="en">
<head>
<meta charset="utf-8">
<title>Quintel Packaging Business Card</title>
<link rel="stylesheet" href="https://fonts.googleapis.com/css2?family=Montserrat:wght@400;500;700&display=swap">
<style>
  :root {
    --page: #ecebe8;
    --card-clear: #f7f6f3;
    --card-edge: #d9d6d0;
    --ink: #2f3033;
    --teal: #1b8493;
    --teal-deep: #15707e;
    --charcoal: #343434;
    --cream: #e6e1d8;
    --white: #ffffff;
  }
  * { margin: 0; padding: 0; box-sizing: border-box; }
  html, body {
    width: 1200px;
    height: 1047px;
    overflow: hidden;
    background: var(--page);
    font-family: "Montserrat", Arial, sans-serif;
  }
  .card {
    position: absolute;
    left: 80px;
    top: 226px;
    width: 1040px;
    height: 594px;
    border-radius: 36px;
    background: var(--card-clear);
    border: 1px solid var(--card-edge);
    overflow: hidden;
  }
  .brand {
    position: absolute;
    left: 56px;
    top: 78px;
    display: flex;
    align-items: center;
    gap: 20px;
  }
  .brand-square {
    width: 56px;
    height: 56px;
    background: var(--teal);
  }
  .brand-name {
    font-size: 42px;
    font-weight: 700;
    color: var(--ink);
    letter-spacing: 0.5px;
  }
  .person {
    position: absolute;
    right: 46px;
    top: 62px;
    text-align: right;
  }
  .person-name {
    font-size: 46px;
    font-weight: 700;
    color: var(--teal);
    letter-spacing: 1px;
    line-height: 1.1;
  }
  .person-title {
    font-size: 25px;
    font-weight: 500;
    color: var(--ink);
    margin-top: 8px;
  }
  .accent-bar {
    position: absolute;
    right: 0;
    top: 68px;
    width: 10px;
    height: 80px;
    background: var(--teal);
  }
  .contact-band {
    position: absolute;
    left: 0;
    bottom: 0;
    width: 100%;
    height: 242px;
    background: linear-gradient(90deg, var(--teal) 0%, var(--teal-deep) 60%, var(--teal) 100%);
  }
  .band-dark {
    position: absolute;
    right: 0;
    top: 0;
    width: 112px;
    height: 100%;
    background: var(--charcoal);
  }
  .band-mark {
    position: absolute;
    right: 48px;
    top: 14px;
    width: 214px;
    height: 214px;
    border-radius: 50%;
    background: var(--cream);
  }
  .contact {
    position: absolute;
    left: 53px;
    top: 14px;
    color: var(--white);
    font-size: 26px;
    font-weight: 400;
    list-style: none;
  }
  .contact li { line-height: 40px; }
  .contact .address-line:nth-child(2) { margin-bottom: 14px; }
  .contact-item { display: flex; align-items: center; gap: 12px; }
  .contact-item svg { width: 20px; height: 20px; fill: var(--white); flex: none; }
</style>
</head>
<body>
  <div class="card">
    <div class="brand">
      <span class="brand-square"></span>
      <span class="brand-name">Quintel Packaging</span>
    </div>

    <div class="person">
      <div class="person-name">MARCUS HALE</div>
      <div class="person-title">Managing Director</div>
    </div>
    <span class="accent-bar"></span>

    <div class="contact-band">
      <span class="band-dark"></span>
      <span class="band-mark"></span>
      <ul class="contact">
        <li class="address-line">Your address, City</li>
        <li class="address-line">State, Zip 1234</li>
        <li class="contact-item">
          <svg viewBox="0 0 20 20" aria-hidden="true"><path d="M2 8c0-3 4-5 8-5s8 2 8 5l-3 1-1-2c-2-1-6-1-8 0L5 9 2 8zM5 11h10l1 5H4l1-5zm5 1.2a1.8 1.8 0 1 0 0 3.6 1.8 1.8 0 0 0 0-3.6z"/></svg>
          <span>123 456 789</span>
        </li>
        <li class="contact-item">
          <svg viewBox="0 0 20 20" aria-hidden="true"><path d="M2 5h16v10H2z M2 5l8 6 8-6" stroke="#1b8493" stroke-width="1.4"/></svg>
          <span>info@yourdomain.com</span>
        </li>
        <li class="contact-item">
          <svg viewBox="0 0 20 20" aria-hidden="true"><circle cx="10" cy="10" r="8"/><path d="M3 9c3 0 4 2 6 1s1-4 4-5M11 17c0-3 2-3 3-5s3-1 4-1" stroke="#1b8493" stroke-width="1.4" fill="none"/></svg>
          <span>www.yourwebsite.com</span>
        </li>
      </ul>
    </div>
  </div>
</body>
</html>
```